Website for my photography business

I need a website for my photography business, Bram Kellet Photography. I need a website that has a landing page with a cover photo of each kind of photography I do. For example, Nature, Weddings, Portraits and Architecture. I want it so that when someone comes onto my website they have to choose which kind of photography page they want to visit. So if they click on the wedding photo it will open to a page with my wedding portfolio images and a contact me button. If they choose nature photography I want them to be redirected to an e-commerce section where they can purchase prints. Architecture and Portraits should open up to their respective portfolios with about me and contact info. I like this kind of format because I want people who come to my website for a specific type of photography to be able to be directed there easily without having to look at a mix of other kinds of photography. I will provide a few files to use as placeholders. I have already purchased the bramkelletphotography.example domain name. A Wix website would be great because I am most familiar with it but I am open to anything.

Industry/Entity Type

Photographer

Number of Pages Required

5+ page

Requirements
Must have
• Landing Page and e-commerce

```html
<!DOCTYPE html>
<html lang="en">
<head>
<meta charset="utf-8">
<title>Bram Kellet Photography – Portraits</title>
<link rel="stylesheet" href="https://fonts.googleapis.com/css2?family=Cormorant+Garamond:ital,wght@0,400;0,500;1,400;1,500&family=Jost:wght@300;400;500&display=swap">
<style>
  :root {
    --accent-line: #a0208a;
    --header-bg: #f7f7f7;
    --page-bg: #ffffff;
    --ink: #2b2b2b;
    --ink-soft: #555555;
    --contact-bg: #c5d6e8;
    --field-bg: #ffffff;
    --button-bg: #000000;
    --button-ink: #ffffff;
  }
  * { margin: 0; padding: 0; box-sizing: border-box; }
  html, body { width: 816px; height: 1200px; overflow: hidden; background: var(--page-bg); }
  body { position: relative; color: var(--ink); font-family: "Jost", sans-serif; }

  .site-header { position: absolute; left: 0; top: 0; width: 816px; height: 127px; background: var(--header-bg); border-top: 1px solid var(--accent-line); }
  .brand-name { position: absolute; top: 25px; width: 100%; text-align: center; font-family: "Cormorant Garamond", serif; font-weight: 500; font-size: 20px; letter-spacing: 0.8px; }
  .brand-sub { position: absolute; top: 53px; width: 100%; text-align: center; font-size: 7.5px; letter-spacing: 6.8px; font-weight: 400; padding-left: 7px; color: var(--ink); }
  .main-nav a { position: absolute; top: 89px; transform: translateX(-50%); font-family: "Cormorant Garamond", serif; font-style: italic; font-size: 10px; color: var(--ink); text-decoration: none; white-space: nowrap; }
  .main-nav a.is-current { color: #777; }

  .section-title { position: absolute; width: 100%; text-align: center; font-family: "Cormorant Garamond", serif; font-style: italic; font-weight: 400; }
  .portraits-title { top: 143px; font-size: 18px; }

  .gallery-main { position: absolute; left: 115px; top: 186px; width: 586px; height: 204px; background: linear-gradient(90deg, #c9c2b8 0%, #b9b0a6 30%, #5a4d48 50%, #8e8a86 72%, #a7a39f 100%); }
  .gallery-next { position: absolute; left: 664px; top: 276px; }
  .thumb-strip { position: absolute; left: 115px; top: 390px; width: 586px; height: 71px; display: flex; overflow: hidden; }
  .thumb { flex: 0 0 72px; height: 71px; }

  .about { position: absolute; left: 0; top: 483px; width: 816px; height: 364px; }
  .about-photo-left { position: absolute; left: 0; top: 0; width: 204px; height: 364px; background: linear-gradient(180deg, #b6bfc2 0%, #9aa29d 45%, #4e6350 75%, #3f5443 100%); }
  .about-photo-right { position: absolute; left: 408px; top: 0; width: 408px; height: 364px; background: linear-gradient(135deg, #4b4550 0%, #c99c86 35%, #b27c66 55%, #8a6a92 70%, #b07a4e 100%); }
  .about-copy { position: absolute; left: 204px; top: 0; width: 204px; text-align: center; }
  .about-title { margin-top: 26px; font-family: "Cormorant Garamond", serif; font-style: italic; font-size: 27px; font-weight: 400; }
  .about-tagline { margin-top: 23px; font-size: 9.5px; letter-spacing: 1px; line-height: 12px; font-weight: 400; }
  .about-text { margin-top: 9px; font-size: 9px; line-height: 15px; font-weight: 300; color: var(--ink-soft); }
  .about-link { display: block; margin-top: 11px; font-family: "Cormorant Garamond", serif; font-style: italic; font-size: 10px; color: var(--ink); text-decoration: none; }

  .contact { position: absolute; left: 0; top: 869px; width: 816px; height: 262px; background: var(--contact-bg); }
  .contact-title { top: 13px; font-size: 17px; }
  .field { position: absolute; left: 277px; width: 274px; background: var(--field-bg); font-size: 7.5px; font-weight: 300; color: var(--ink); padding: 4px 7px; }
  .field-name { top: 54px; height: 18px; }
  .field-email { top: 79px; height: 18px; }
  .field-subject { top: 103px; height: 18px; }
  .field-message { top: 128px; height: 75px; padding-top: 6px; padding-left: 9px; }
  .submit-btn { position: absolute; left: 369px; top: 193px; width: 89px; height: 33px; background: var(--button-bg); color: var(--button-ink); font-size: 9.5px; font-weight: 400; display: flex; align-items: center; justify-content: center; }

  .site-footer { position: absolute; left: 0; top: 1131px; width: 816px; height: 69px; }
  .social-links { position: absolute; top: 24px; left: 0; width: 100%; display: flex; justify-content: center; gap: 14px; }
  .social-link { font-size: 7.5px; font-weight: 400; color: var(--ink); text-decoration: none; line-height: 10px; }
  .copyright { position: absolute; top: 43px; width: 100%; text-align: center; font-size: 7.5px; font-weight: 300; color: var(--ink-soft); }
</style>
</head>
<body>
  <header class="site-header">
    <div class="brand-name">BRAM KELLET</div>
    <div class="brand-sub">PHOTOGRAPHY</div>
    <nav class="main-nav">
      <a href="#" style="left:177px">Architecture</a>
      <a href="#" class="is-current" style="left:294px">Portraits</a>
      <a href="#" style="left:406px">Weddings</a>
      <a href="#" style="left:514px">Nature</a>
      <a href="#" style="left:633px">Book a Session</a>
    </nav>
  </header>

  <h1 class="section-title portraits-title">Portraits</h1>

  <div class="gallery-main" role="img" aria-label="Featured portrait: smiling woman with curly hair and sunglasses on a sunny street"></div>
  <svg class="gallery-next" width="14" height="22" viewBox="0 0 14 22" aria-hidden="true"><polyline points="2,1 12,11 2,21" fill="none" stroke="#ffffff" stroke-width="1.3"/></svg>
  <div class="thumb-strip">
    <div class="thumb" role="img" aria-label="Portrait thumbnail: woman on street" style="background:linear-gradient(#c9c6c0,#6d7d92)"></div>
    <div class="thumb" role="img" aria-label="Portrait thumbnail: young woman, light backdrop" style="background:linear-gradient(#e9e6e2,#5b4a40)"></div>
    <div class="thumb" role="img" aria-label="Portrait thumbnail: woman against red background" style="background:linear-gradient(90deg,#c8281f,#c89a74,#b0342a)"></div>
    <div class="thumb" role="img" aria-label="Portrait thumbnail: woman in red sweater" style="background:linear-gradient(#d8d2cc,#a01c2a)"></div>
    <div class="thumb" role="img" aria-label="Portrait thumbnail: woman in city at dusk" style="background:linear-gradient(#a89a8c,#2e2a28)"></div>
    <div class="thumb" role="img" aria-label="Portrait thumbnail: curly-haired woman by blue wall" style="background:linear-gradient(90deg,#9bb9d6,#b98a64,#a8c4dc)"></div>
    <div class="thumb" role="img" aria-label="Portrait thumbnail: man on dark background" style="background:linear-gradient(#1c1c1c,#4a4644)"></div>
    <div class="thumb" role="img" aria-label="Portrait thumbnail: red-haired woman by lake" style="background:linear-gradient(#9fb6c4,#c77f5a,#3b4560)"></div>
    <div class="thumb" role="img" aria-label="Portrait thumbnail" style="background:linear-gradient(#e4e2de,#222)"></div>
  </div>

  <section class="about">
    <div class="about-photo-left" role="img" aria-label="Portrait: woman in white hoodie beside a football goal net"></div>
    <div class="about-copy">
      <h2 class="about-title">About me</h2>
      <p class="about-tagline">THIS IS A GREAT PLACE FOR<br>YOUR TAGLINE.</p>
      <p class="about-text">Tell your visitors your<br>story. Add catchy text<br>to describe what you<br>do, and what you have<br>to offer. The right words<br>can inspire and intrigue<br>your audience, so<br>they’re ready to take<br>action on your site. To<br>start telling your story,<br>double click or click<br>Edit Text.</p>
      <a href="#" class="about-link">Book a place &gt;</a>
    </div>
    <div class="about-photo-right" role="img" aria-label="Close portrait: woman with lilac hair in a camel turtleneck and coat"></div>
  </section>

  <section class="contact">
    <h2 class="section-title contact-title">Contact me</h2>
    <div class="field field-name">Name</div>
    <div class="field field-email">Email</div>
    <div class="field field-subject">Subject</div>
    <div class="field field-message">Type your message here...</div>
    <div class="submit-btn">Submit</div>
  </section>

  <footer class="site-footer">
    <nav class="social-links" aria-label="Social links">
      <a href="#" class="social-link">Friendwall</a>
      <a href="#" class="social-link">Chirpline</a>
      <a href="#" class="social-link">Pinboardly</a>
      <a href="#" class="social-link">Snapframe</a>
    </nav>
    <p class="copyright">© 2023 by Bram Kellet Photography</p>
  </footer>
</body>
</html>
```